Law Firm Business Card

This is a business card for a law firm that serves US military and veterans.

The card must have ONLY the following (we want an uncluttered look):

- Company logo (PNG, GIF, JPEG copies uploaded)
- A tagline reading: "a law firm for service members and veterans"
- My name and title: "Tobias Marlow" and "Attorney"
- My email: "tobias.marlow@brinmoorlegal.com"
- My number: "855-FIRM-ONE (347-6663)"

We are looking for a clean, simple layout with only the above information, likely printed on a bright white cotton stock. The font of our logo is DIN 1451, and the font used on our website is Helvetica Neue. The color of our logo is #336699, and we probably want the tagline in that color also, and my contact information in a dark grey. Please review our website at www.brinmoorlegal.com to ensure your card design complements our website style.

Thanks and we look forward to seeing your submissions.

A few notes:

- Two-sided submissions are ok
- Please don't add graphics (scales of justice, judges hammer, etc)

```html
<!DOCTYPE html>
<html lang="en">
<head>
<meta charset="utf-8">
<title>Brinmoor Legal — Business Card</title>
<link href="https://fonts.googleapis.com/css2?family=Inter:wght@300;400;600&display=swap" rel="stylesheet">
<style>
  :root {
    --brand-blue: #336699;
    --ink-grey: #555a60;
    --ink-soft: #6b7076;
    --paper: #ffffff;
    --backdrop: #b9b9b9;
  }
  * { box-sizing: border-box; margin: 0; padding: 0; }
  html, body {
    width: 1200px;
    height: 720px;
    overflow: hidden;
    background: var(--backdrop);
    font-family: "Inter", "Helvetica Neue", Arial, sans-serif;
  }
  .canvas {
    width: 1200px;
    height: 720px;
    display: flex;
    align-items: center;
    justify-content: center;
  }
  .business-card {
    position: relative;
    width: 1000px;
    height: 572px;
    background: var(--paper);
    box-shadow: 0 10px 30px rgba(0,0,0,0.18);
    overflow: hidden;
  }
  .firm-name {
    position: absolute;
    top: 92px;
    left: 0;
    right: 0;
    text-align: center;
    padding-left: 90px;
    font-weight: 600;
    font-size: 84px;
    letter-spacing: 1px;
    text-transform: uppercase;
    color: var(--brand-blue);
    line-height: 1;
  }
  .tagline-band {
    position: absolute;
    top: 262px;
    left: 0;
    width: 968px;
    height: 62px;
    background: var(--brand-blue);
    display: flex;
    align-items: center;
    justify-content: center;
  }
  .tagline {
    color: var(--paper);
    font-weight: 300;
    font-size: 27px;
    letter-spacing: 0.3px;
  }
  .person {
    position: absolute;
    left: 72px;
    bottom: 92px;
    color: var(--ink-grey);
  }
  .person-name {
    font-weight: 300;
    font-size: 44px;
    line-height: 1.1;
  }
  .person-title {
    font-weight: 300;
    font-size: 25px;
    margin-top: 6px;
    color: var(--ink-soft);
  }
  .contact-list {
    position: absolute;
    left: 520px;
    top: 372px;
    list-style: none;
    color: var(--ink-grey);
  }
  .contact-item {
    display: flex;
    align-items: center;
    gap: 16px;
    font-weight: 300;
    font-size: 23px;
    margin-bottom: 20px;
  }
  .contact-icon {
    width: 34px;
    height: 34px;
    flex: none;
  }
</style>
</head>
<body>
  <main class="canvas">
    <article class="business-card">
      <h1 class="firm-name">Brinmoor Legal</h1>

      <div class="tagline-band">
        <p class="tagline">a law firm for service members and veterans</p>
      </div>

      <ul class="contact-list">
        <li class="contact-item">
          <svg class="contact-icon" viewBox="0 0 34 34" aria-hidden="true">
            <circle cx="17" cy="17" r="17" fill="var(--brand-blue)"/>
            <path d="M11.5 9.5c1-.6 2-.3 2.5.6l1.5 2.8c.4.8.2 1.6-.5 2.1l-1 .8c.9 2 2.4 3.5 4.4 4.4l.8-1c.5-.7 1.3-.9 2.1-.5l2.8 1.5c.9.5 1.2 1.5.6 2.5l-.8 1.3c-.7 1.1-2 1.6-3.2 1.2-4.9-1.6-8.5-5.2-10.1-10.1-.4-1.2.1-2.5 1.2-3.2z" fill="#fff"/>
          </svg>
          <span class="contact-text">855-FIRM-ONE (347-6663)</span>
        </li>
        <li class="contact-item">
          <svg class="contact-icon" viewBox="0 0 34 34" aria-hidden="true">
            <circle cx="17" cy="17" r="17" fill="var(--brand-blue)"/>
            <rect x="8.5" y="11" width="17" height="12" rx="1.2" fill="#fff"/>
            <path d="M9 11.8l8 6.2 8-6.2" fill="none" stroke="var(--brand-blue)" stroke-width="1.6"/>
          </svg>
          <span class="contact-text">tobias.marlow@brinmoorlegal.com</span>
        </li>
      </ul>

      <div class="person">
        <p class="person-name">Tobias Marlow</p>
        <p class="person-title">Attorney</p>
      </div>
    </article>
  </main>
</body>
</html>
```